Timber Crest Construction Needs business card

Hey we are in need of business card designs. I have upload our logo as a guideline, but free feel to run with it or come up with something unique.
Pls have fun with it and be creative. the name says it all!
i will give some directions after i see a few entries..
Updates
Logo source file has been uploaded..
Hey because of the logo is so colourful already.
Can we have a few submissions with less colour.
Also we are looking for clever/hidden/descriptive business card.

```html
<!DOCTYPE html>
<html lang="en">
<head>
<meta charset="utf-8">
<title>Timber Crest Construction – Business Card</title>
<link href="https://fonts.googleapis.com/css2?family=Montserrat:wght@400;600&family=Roboto:wght@400&display=swap" rel="stylesheet">
<style>
  :root {
    --page-bg: #ece9e4;
    --card-white: #ffffff;
    --swoosh-black: #1c1c1c;
    --swoosh-grey: #bdbdbd;
    --swoosh-light: #e6e6e6;
    --brand-grey: #5e5e5e;
    --text-dark: #333333;
    --text-mid: #555555;
  }
  * { margin: 0; padding: 0; box-sizing: border-box; }
  html, body { width: 1200px; height: 913px; overflow: hidden; }
  body { background: var(--page-bg); position: relative; font-family: "Roboto", Arial, sans-serif; }

  .card {
    position: absolute;
    width: 540px;
    height: 310px;
    background: var(--card-white);
    overflow: hidden;
    box-shadow: 0 6px 18px rgba(0,0,0,0.18);
  }
  .card-front { left: 50px; top: 120px; }
  .card-back  { left: 610px; top: 480px; }
  .card-swooshes { position: absolute; inset: 0; width: 100%; height: 100%; }

  .brand-name {
    position: absolute;
    font-family: "Montserrat", Arial, sans-serif;
    font-weight: 600;
    color: var(--brand-grey);
    letter-spacing: 0.02em;
    line-height: 1;
    white-space: nowrap;
  }
  .card-front .brand-name { left: 70px; top: 112px; font-size: 40px; }
  .card-front .brand-tagline { left: 72px; top: 160px; font-size: 14px; letter-spacing: 0.3em; }
  .card-back .brand-name { left: 34px; top: 150px; font-size: 22px; }
  .card-back .brand-tagline { left: 35px; top: 178px; font-size: 8.5px; letter-spacing: 0.3em; }
  .brand-mark {
    position: absolute;
    background: var(--brand-grey);
  }
  .card-front .brand-mark { left: 70px; top: 80px; width: 22px; height: 22px; }
  .card-back .brand-mark { left: 34px; top: 128px; width: 13px; height: 13px; }

  .contact-block { position: absolute; left: 300px; top: 78px; color: var(--text-dark); }
  .contact-name { font-size: 18px; color: var(--text-dark); }
  .contact-title { font-size: 9px; color: var(--text-mid); margin: 2px 0 10px; }
  .contact-list { list-style: none; }
  .contact-list li {
    display: flex; align-items: center; gap: 10px;
    font-size: 10.5px; color: var(--text-dark); height: 20px;
  }
  .contact-list svg { width: 12px; height: 12px; fill: var(--text-dark); flex: none; }
</style>
</head>
<body>

<section class="card card-front" aria-label="Business card front">
  <svg class="card-swooshes" viewBox="0 0 540 310" preserveAspectRatio="none" aria-hidden="true">
    <defs>
      <linearGradient id="front-grey" x1="0" y1="0" x2="1" y2="0">
        <stop offset="0" stop-color="#ffffff"/>
        <stop offset="1" stop-color="#a9a9a9"/>
      </linearGradient>
    </defs>
    <path d="M120 0 H540 V58 Q380 10 120 0 Z" fill="url(#front-grey)"/>
    <path d="M0 225 Q240 300 540 232 V252 Q260 316 0 246 Z" fill="var(--swoosh-light)"/>
    <path d="M0 246 Q260 316 540 252 V310 H0 Z" fill="var(--swoosh-black)"/>
  </svg>
  <span class="brand-mark"></span>
  <span class="brand-name">TIMBER CREST</span>
  <span class="brand-name brand-tagline">CONSTRUCTION</span>
</section>

<section class="card card-back" aria-label="Business card back">
  <svg class="card-swooshes" viewBox="0 0 540 310" preserveAspectRatio="none" aria-hidden="true">
    <defs>
      <linearGradient id="back-grey" x1="0" y1="0" x2="1" y2="0">
        <stop offset="0" stop-color="#9a9a9a"/>
        <stop offset="1" stop-color="#eeeeee"/>
      </linearGradient>
    </defs>
    <path d="M0 0 H540 V18 Q260 8 0 70 Z" fill="url(#back-grey)"/>
    <path d="M0 0 H170 Q70 14 0 52 Z" fill="var(--swoosh-black)"/>
    <path d="M540 150 Q510 260 380 310 H540 Z" fill="var(--swoosh-light)"/>
    <path d="M540 170 Q520 268 420 310 H540 Z" fill="var(--swoosh-black)"/>
  </svg>
  <span class="brand-mark"></span>
  <span class="brand-name">TIMBER CREST</span>
  <span class="brand-name brand-tagline">CONSTRUCTION</span>

  <div class="contact-block">
    <p class="contact-name">Your Name</p>
    <p class="contact-title">Title</p>
    <ul class="contact-list">
      <li><svg viewBox="0 0 12 12"><path d="M6 0a4 4 0 0 1 4 4c0 3-4 8-4 8S2 7 2 4a4 4 0 0 1 4-4zm0 2.5a1.5 1.5 0 1 0 0 3 1.5 1.5 0 0 0 0-3z"/></svg>Your Commercial or office address</li>
      <li><svg viewBox="0 0 12 12"><path d="M1 3q5-3 10 0v2H8.5V4h-5v1H1zM3 6h6l2 5H1z"/></svg>00.00.00.0000</li>
      <li><svg viewBox="0 0 12 12"><path d="M3 0h5v4H3zM1 4h10v8H1zm2 2v1h6V6zm0 3v1h6V9z"/></svg>00.00.00.0000</li>
      <li><svg viewBox="0 0 12 12"><path d="M0 2h12v1L6 7 0 3zm0 2.5 6 4 6-4V10H0z"/></svg>yourname@yourwebsite.com</li>
      <li><svg viewBox="0 0 12 12"><path d="M6 0a6 6 0 1 0 0 12A6 6 0 0 0 6 0zm-1 1.2C4 2.6 3.6 4 3.5 5.4H1.3A4.8 4.8 0 0 1 5 1.2zm2 0a4.8 4.8 0 0 1 3.7 4.2H8.5C8.4 4 8 2.6 7 1.2zM4.6 5.4C4.7 3.9 5.2 2.5 6 1.5c.8 1 1.3 2.4 1.4 3.9zm-3.3 1.2h2.2c.1 1.4.5 2.8 1.5 4.2a4.8 4.8 0 0 1-3.7-4.2zm3.3 0h2.8c-.1 1.5-.6 2.9-1.4 3.9-.8-1-1.3-2.4-1.4-3.9zm3.9 0h2.2A4.8 4.8 0 0 1 7 10.8c1-1.4 1.4-2.8 1.5-4.2z"/></svg>www.yourwebsite.com</li>
    </ul>
  </div>
</section>

</body>
</html>
```